New business card/stationary for a consulting company

I am looking for a clean and very professional looking business card for my consulting company as well as corresponding stationary. I am uploading our logo. I like simple and powerful for the feel. No graphics but I am open on everything else. Below is my contact information but would like the final to be in a version I can add my employees information into and print. Thank you.

Daniel Whitcombe
dan@ferncliffadvisory.com
2870 North 9th Avenue, Summit Floor, Elm Ridge, Illinois 60531
www.ferncliffadvisory.com

Industry/Entity Type

Consulting

Contact Information for Business Card

Daniel Whitcombe
dan@ferncliffadvisory.com
www.ferncliffadvisory.com

Font styles to use
Serif
Sans Serif

Requirements
Must have
• Our logo and the business card details.
Nice to have
• our website www.ferncliffadvisory.com

```html
<!DOCTYPE html>
<html lang="en">
<head>
<meta charset="utf-8">
<title>Ferncliff Advisory — Business Card</title>
<link rel="stylesheet" href="https://fonts.googleapis.com/css2?family=Lato:wght@400;700&display=swap">
<style>
  :root {
    --backdrop: #2a2a2c;
    --card: #ffffff;
    --navy: #070a6b;
    --ink: #1a1a1a;
  }
  * { box-sizing: border-box; margin: 0; padding: 0; }
  html, body {
    width: 1200px; height: 900px; overflow: hidden;
    background: var(--backdrop);
    font-family: "Lato", Arial, sans-serif;
  }
  .canvas { position: relative; width: 1200px; height: 900px; }
  .card {
    position: absolute; left: 250px; width: 700px; height: 400px;
    background: var(--card); overflow: hidden;
  }
  .card--front { top: 35px; }
  .card--back { top: 465px; }

  .wordmark {
    color: var(--navy); font-weight: 400; text-transform: uppercase;
    letter-spacing: 0.08em; white-space: nowrap;
    display: flex; align-items: center; gap: 14px;
  }
  .wordmark__square { width: 18px; height: 18px; background: var(--navy); flex: none; }

  .card--front .wordmark {
    position: absolute; top: 50%; left: 50%; transform: translate(-50%, -50%);
    font-size: 38px;
  }

  .back__info { position: absolute; left: 0; top: 0; width: 400px; height: 400px; padding: 52px 0 0 40px; }
  .back__info .wordmark { font-size: 25px; }
  .address { margin-top: 74px; font-size: 19px; line-height: 1.25; color: var(--ink); }
  .contact { margin-top: 20px; list-style: none; font-size: 19px; color: var(--ink); }
  .contact li { display: flex; align-items: center; gap: 14px; line-height: 1.5; }
  .contact svg { width: 18px; height: 18px; flex: none; }

  .back__panel {
    position: absolute; left: 400px; top: 0; width: 260px; height: 400px;
    background: var(--navy); padding: 52px 0 0 22px;
  }
  .back__name { color: #fff; font-weight: 700; font-size: 27px; white-space: nowrap; }
  .back__rule {
    position: absolute; left: 667px; top: 0; width: 4px; height: 400px; background: var(--navy);
  }
</style>
</head>
<body>
<main class="canvas">
  <section class="card card--front" aria-label="Card front">
    <div class="wordmark"><span class="wordmark__square"></span>Ferncliff Advisory</div>
  </section>

  <section class="card card--back" aria-label="Card back">
    <div class="back__info">
      <div class="wordmark"><span class="wordmark__square"></span>Ferncliff Advisory</div>
      <address class="address" style="font-style:normal">
        2870 North 9th Avenue<br>
        Summit Floor<br>
        Elm Ridge, Illinois 60531
      </address>
      <ul class="contact">
        <li>
          <svg viewBox="0 0 18 18" aria-hidden="true">
            <rect x="1" y="4" width="16" height="11" fill="var(--navy)"/>
            <path d="M1 4 L9 10 L17 4" fill="none" stroke="#fff" stroke-width="1.4"/>
          </svg>
          dan@ferncliffadvisory.com
        </li>
        <li>
          <svg viewBox="0 0 18 18" aria-hidden="true">
            <circle cx="9" cy="9" r="7.5" fill="var(--navy)"/>
            <g fill="none" stroke="#fff" stroke-width="1">
              <ellipse cx="9" cy="9" rx="3.2" ry="7.5"/>
              <line x1="1.5" y1="9" x2="16.5" y2="9"/>
              <line x1="9" y1="1.5" x2="9" y2="16.5"/>
            </g>
          </svg>
          www.ferncliffadvisory.com
        </li>
      </ul>
    </div>
    <div class="back__panel">
      <p class="back__name">Daniel Whitcombe</p>
    </div>
    <div class="back__rule"></div>
  </section>
</main>
</body>
</html>
```